Designing a brochures for an educational counseling service provider

We would like a 4 sided design on a 11x8.5 paper, half folded. I have including a sample design we did to give you an idea of what we envision but we welcome creativity to make beautiful looking flyers. Text for the flier is included as well as our logo.
- The most important thing is capturing our audience/market. We will be handing these flies to schools, organizations and individual clients.

www.pvrlearningadvisors.example

Target Market(s)

We are targeting international students wanting to study in the U.S and Canada.

Industry/Entity Type

Education

Requirements
Must have
• - Clean and clear
• - Our logo should visible and well placed.
• - Could you the pictures of students, libraries and school buildings or you could use the pictures we already have.
Nice to have
• We would like this to match business cards.

```html
<!DOCTYPE html>
<html lang="en">
<head>
<meta charset="utf-8">
<title>Educational Consulting Brochure – Inside Spread</title>
<link rel="stylesheet" href="https://fonts.googleapis.com/css2?family=Open+Sans:ital,wght@0,600;0,700;1,700&family=Raleway:wght@400;500;600&display=swap">
<style>
  :root {
    --backdrop: #e9e6e1;
    --paper: #ffffff;
    --ink: #2c2c34;
    --navy: #2a2a82;
    --blue: #1e6ec4;
    --green-dark: #39b54a;
    --green-light: #8dc63f;
    --photo-study: #5a4a44;
    --photo-library: #3f4a66;
    --photo-students: #b9a88e;
  }
  * { box-sizing: border-box; margin: 0; padding: 0; }
  html, body { width: 1200px; height: 900px; overflow: hidden; }
  body {
    background: var(--backdrop);
    font-family: "Raleway", sans-serif;
    color: var(--ink);
    position: relative;
  }
  .spread {
    position: absolute;
    left: 60px; top: 33px;
    width: 1080px; height: 834px;
    display: flex;
    box-shadow: 0 6px 24px rgba(0,0,0,.18);
  }
  .page {
    position: relative;
    width: 540px; height: 834px;
    background: var(--paper);
    overflow: hidden;
  }
  .page--left { border-right: 1px solid #ddd; }

  .section-tab {
    position: absolute;
    font-family: "Open Sans", sans-serif;
    font-weight: 700;
    color: #fff;
    background: linear-gradient(90deg, var(--green-dark), var(--green-light));
    clip-path: polygon(0 0, 100% 0, 88% 100%, 0 100%);
    display: flex; align-items: center;
    padding-left: 22px;
  }
  .section-tab--main { height: 48px; font-size: 18px; }

  .photo {
    position: absolute;
  }
  .photo--study {
    left: 230px; top: 0; width: 310px; height: 165px;
    background: linear-gradient(135deg, #3a2f2c, var(--photo-study) 55%, #c9a47e);
  }
  .photo--library {
    left: 0; top: 410px; width: 540px; height: 380px;
    background: linear-gradient(160deg, #16182a, var(--photo-library) 45%, #d7dbe6 80%, #8b93a8);
  }
  .photo--students {
    left: 150px; top: 22px; width: 390px; height: 130px;
    background: linear-gradient(120deg, #8a9a6a, var(--photo-students) 50%, #d9cdb8);
  }

  .body-copy {
    position: absolute;
    font-size: 11px;
    line-height: 1.42;
  }
  .body-copy p + p { margin-top: 9px; }

  .about-copy { left: 42px; top: 180px; width: 460px; text-align: justify; }

  .quote-band {
    position: absolute;
    left: 0; top: 330px; width: 540px; height: 96px;
    background: linear-gradient(90deg, var(--navy), var(--blue));
    clip-path: polygon(0 18%, 100% 0, 100% 78%, 0 100%);
    display: flex; align-items: center; justify-content: center;
    padding: 0 40px;
  }
  .quote-band q {
    font-family: "Open Sans", sans-serif;
    font-style: italic; font-weight: 700;
    font-size: 15px; line-height: 1.3;
    color: #fff; text-align: center;
    quotes: "\201C" "\201D";
  }

  .footer-wave {
    position: absolute; left: 0; bottom: 0;
    width: 540px; height: 70px;
  }

  .services-copy { left: 36px; top: 168px; width: 470px; }
  .services-copy .intro { text-align: justify; }
  .package-list { list-style: none; margin-top: 4px; }
  .package-list li { position: relative; padding-left: 14px; }
  .package-list li::before {
    content: ""; position: absolute; left: 0; top: 4px;
    width: 7px; height: 7px; background: var(--blue);
  }
  .sub-heading {
    display: inline-block;
    font-family: "Open Sans", sans-serif;
    font-weight: 700; font-size: 13px;
    color: #fff;
    background: linear-gradient(90deg, var(--green-dark), var(--green-light));
    clip-path: polygon(0 0, 100% 0, 90% 100%, 0 100%);
    padding: 3px 26px 3px 10px;
    margin: 14px 0 6px;
  }
  .justified { text-align: justify; }
</style>
</head>
<body>
<main class="spread">

  <section class="page page--left">
    <div class="photo photo--study" role="img" aria-label="Photo of students studying together in a library"></div>
    <h2 class="section-tab section-tab--main" style="left:40px;top:28px;width:170px;">About Us</h2>

    <div class="body-copy about-copy">
      <p>Our mission is to make quality education accessible and affordable to the families we serve. Our services are designed with the child's future in mind. Whether one is seeking an academic or non-academic environment, it is important to us that we set our clients up for success.</p>
      <p>We are a family-centered organization and our goals are the same as those of our clients: for their child to thrive and reach their goals and dreams. With over 10 years of experience in the business, we are aware of the financial obstacles created by the ever increasing cost in education. Our expert consultants work closely with families to map out their educational budget and find the best affordable and quality educational options.</p>
    </div>

    <div class="photo photo--library" role="img" aria-label="Photo of a curved wall of library bookshelves with railings"></div>

    <div class="quote-band">
      <q>We offer comprehensive services to families, students, institutions and governmental organizations.</q>
    </div>

    <svg class="footer-wave" viewBox="0 0 540 70" preserveAspectRatio="none" aria-hidden="true">
      <defs>
        <linearGradient id="waveLeft" x1="0" x2="1">
          <stop offset="0" stop-color="#2a2a82"/>
          <stop offset="1" stop-color="#1e6ec4"/>
        </linearGradient>
      </defs>
      <path d="M0 14 Q270 40 540 56 L540 70 L0 70 Z" fill="#fff"/>
      <path d="M0 22 Q270 50 540 62 L540 70 L0 70 Z" fill="url(#waveLeft)"/>
    </svg>
  </section>

  <section class="page page--right">
    <div class="photo photo--students" role="img" aria-label="Photo of smiling students standing outdoors"></div>
    <h2 class="section-tab section-tab--main" style="left:0;top:40px;width:165px;">Services</h2>

    <div class="body-copy services-copy">
      <p class="intro">Finding the right school or program for your child is one of the most important decisions your family will make. The right choice will make a major impact on your child's future.</p>
      <p>Our package includes</p>
      <ul class="package-list">
        <li>Intake interview</li>
        <li>Present range of options based on needs and goals of the family</li>
        <li>Interview coaching</li>
        <li>Assistance with application and essays</li>
        <li>Updates on student progress throughout their enrollment with the school</li>
        <li>Advisement on financial documents and visa applications</li>
      </ul>

      <h3 class="sub-heading">Boarding schools</h3>
      <p class="justified">Students who want the best out of their grade school experience are likely to choose boarding schools because they are proven to better prepare students for university. North American boarding schools provide a quality dynamic experience that will facilitate personal growth in independence, leadership, and confidence as well as provide the academic curriculum necessary to prepare students for university.</p>

      <h3 class="sub-heading">College admission:</h3>
      <p class="justified">As Educational Consultants, we specialize in college/university admissions and we understand how confusing, time-consuming, and stressful the application process can be. Our experienced counselors are here to answer your questions and guide you step by step. As Parents and students may have limited access to information on schools, may not know or understand the entire process as a whole, nor where/how to begin, our experts counselors have a solutions.</p>
      <p class="justified">Clients increase the odds of admissions with our comprehensive plan of action. We believe that regardless of a student's level of involvement in extra-curricular activities or preparedness, they still possess something they can offer to the university; therefore we help them shine on their college applications.</p>
    </div>

    <svg class="footer-wave" viewBox="0 0 540 70" preserveAspectRatio="none" aria-hidden="true">
      <defs>
        <linearGradient id="waveRight" x1="0" x2="1">
          <stop offset="0" stop-color="#2a2a82"/>
          <stop offset="1" stop-color="#1e6ec4"/>
        </linearGradient>
      </defs>
      <path d="M0 56 Q270 40 540 30 L540 70 L0 70 Z" fill="url(#waveRight)"/>
    </svg>
  </section>

</main>
</body>
</html>
```